Using attached logo that has been created

Business card with logo that's attached. Maybe with water or the cartoon van in background. Looking for it to not be so plain and not too white.
Information to include;
Rodney Ashcombe
(555) 218-7730
Info@bramleypipeworks.example
www.bramleypipeworks.example
License # 4627195
Looking forward to the designs u come up with.
Thank you!
-Delphine
Target Market(s)
Plumbing
Industry/Entity Type
Plumbing
Contact Information for Business Card
Listed above

```html
<!DOCTYPE html>
<html lang="en">
<head>
<meta charset="utf-8">
<title>Bramley Pipeworks – Business Card</title>
<link rel="stylesheet" href="https://fonts.googleapis.com/css2?family=Krona+One&family=Roboto:wght@400&display=swap">
<style>
  :root {
    --page-bg: #2a2b2d;
    --card-bg: #1e1f21;
    --card-edge: #2c2d30;
    --brand-blue: #1a5bbf;
    --brand-yellow: #f5b800;
    --text-light: #ffffff;
    --rule: #8a8b8e;
    --mascot-a: #2f5fae;
    --mascot-b: #8a6f4a;
    --pattern-a: #26272a;
    --pattern-b: #3a3b3f;
  }
  * { box-sizing: border-box; margin: 0; padding: 0; }
  html, body { width: 1200px; height: 1108px; overflow: hidden; }
  body {
    background: var(--page-bg);
    font-family: "Roboto", Arial, sans-serif;
    position: relative;
  }
  .card {
    position: absolute;
    top: 194px;
    width: 440px;
    height: 720px;
    background: var(--card-bg);
    border-radius: 22px;
    box-shadow: 0 20px 40px rgba(0,0,0,.45);
    overflow: hidden;
  }
  .card--front { left: 120px; }
  .card--back { left: 640px; }

  .mascot {
    position: absolute;
    left: 110px; top: 70px;
    width: 220px; height: 250px;
    border-radius: 16px;
    background: linear-gradient(180deg, var(--mascot-a) 0%, var(--mascot-b) 100%);
    opacity: .85;
  }
  .brand-name {
    position: absolute;
    left: 0; right: 0; top: 340px;
    text-align: center;
    font-family: "Krona One", Arial, sans-serif;
    font-size: 24px;
    line-height: 1.25;
    color: var(--brand-blue);
  }
  .person-name {
    position: absolute;
    left: 0; right: 0; top: 430px;
    text-align: center;
    font-family: "Krona One", Arial, sans-serif;
    font-size: 22px;
    letter-spacing: 1px;
    color: var(--brand-blue);
  }
  .icon-row {
    position: absolute;
    left: 40px; right: 40px; top: 478px;
    display: flex; align-items: center; gap: 10px;
  }
  .icon-row .rule { flex: 1; height: 1px; background: var(--rule); }
  .icon-box {
    width: 34px; height: 34px;
    background: var(--brand-blue);
    border-radius: 5px;
    display: flex; align-items: center; justify-content: center;
  }
  .contact {
    position: absolute;
    left: 0; right: 0; top: 530px;
    text-align: center;
    color: var(--text-light);
    font-size: 19px;
    line-height: 1.45;
    list-style: none;
  }
  .divider {
    position: absolute;
    left: 50px; right: 50px; top: 632px;
    height: 1px; background: var(--rule);
  }
  .license {
    position: absolute;
    left: 0; right: 0; top: 650px;
    text-align: center;
    font-size: 19px;
    color: var(--brand-blue);
  }
  .license-number { color: var(--brand-yellow); }

  .back-pattern {
    position: absolute; inset: 0;
    background: linear-gradient(150deg, var(--pattern-b) 0%, var(--pattern-a) 55%, #151617 100%);
  }
  .back-brand {
    position: absolute;
    left: 0; right: 0; top: 420px;
    text-align: center;
    font-family: "Krona One", Arial, sans-serif;
    font-size: 22px;
    line-height: 1.3;
    color: var(--brand-blue);
  }
</style>
</head>
<body>
  <section class="card card--front">
    <div class="mascot" role="img" aria-label="Cartoon mascot of a plumber holding a wrench and a circular saw"></div>
    <div class="brand-name">BRAMLEY<br>PIPEWORKS</div>
    <h1 class="person-name">RODNEY ASHCOMBE</h1>
    <div class="icon-row">
      <span class="rule"></span>
      <span class="icon-box">
        <svg width="20" height="20" viewBox="0 0 24 24" fill="#111"><path d="M6.6 10.8a15 15 0 0 0 6.6 6.6l2.2-2.2a1 1 0 0 1 1-.25 11.4 11.4 0 0 0 3.6.57 1 1 0 0 1 1 1V20a1 1 0 0 1-1 1A17 17 0 0 1 3 4a1 1 0 0 1 1-1h3.5a1 1 0 0 1 1 1c0 1.25.2 2.45.57 3.57a1 1 0 0 1-.25 1z"/></svg>
      </span>
      <span class="icon-box">
        <svg width="20" height="20" viewBox="0 0 24 24" fill="none" stroke="#111" stroke-width="2"><rect x="3" y="5" width="18" height="14" rx="1"/><path d="M3 6l9 7 9-7"/></svg>
      </span>
      <span class="icon-box">
        <svg width="20" height="20" viewBox="0 0 24 24" fill="none" stroke="#111" stroke-width="2"><circle cx="12" cy="12" r="9"/><path d="M3 12h18M12 3c3 3 3 15 0 18M12 3c-3 3-3 15 0 18"/></svg>
      </span>
      <span class="rule"></span>
    </div>
    <ul class="contact">
      <li>(555) 218-7730</li>
      <li>Info@bramleypipeworks.example</li>
      <li>www.bramleypipeworks.example</li>
    </ul>
    <div class="divider"></div>
    <p class="license">License <span class="license-number"># 4627195</span></p>
  </section>

  <section class="card card--back">
    <div class="back-pattern" role="img" aria-label="Faint repeating brand pattern in dark greys"></div>
    <div class="back-brand">BRAMLEY<br>PIPEWORKS</div>
  </section>
</body>
</html>
```